Roofing Contractor business card redesign

I want to redesign my business card with a fresh, eye catching concept

Target Market(s)

Residential Roofing Clients, potential employees, and subcontractors.

Industry/Entity Type

Business

Colors

Designer to choose colors to be used in the design.

Requirements
Nice to have
• I just want something that's more pleasing to the eye. You can use a combination of either / or of my logos.

```html
<!DOCTYPE html>
<html lang="en">
<head>
<meta charset="utf-8">
<title>True North General Contractors – Business Card</title>
<link href="https://fonts.googleapis.com/css2?family=Oswald:wght@500;600&family=Open+Sans:wght@400&display=swap" rel="stylesheet">
<style>
  :root {
    --backdrop: #ecebe8;
    --card-brown: #3a1f1d;
    --card-orange: #e87224;
    --ink-light: #ffffff;
    --ink-dark: #3a1f1d;
    --art-warm: #f2a62a;
    --art-deep: #e06f1f;
  }
  html, body {
    margin: 0;
    width: 1200px;
    height: 900px;
    overflow: hidden;
    background: var(--backdrop);
  }
  .canvas { position: relative; width: 1200px; height: 900px; }

  .card {
    position: absolute;
    box-shadow: 0 8px 24px rgba(0,0,0,.18);
    overflow: hidden;
  }

  /* Contact side */
  .card-contact {
    left: 78px; top: 35px;
    width: 588px; height: 363px;
    background: var(--card-brown);
    color: var(--ink-light);
    font-family: "Open Sans", sans-serif;
  }
  .person-name {
    position: absolute; left: 29px; top: 48px; margin: 0;
    font-family: "Oswald", sans-serif; font-weight: 500;
    font-size: 25px; line-height: 1;
  }
  .person-titles {
    position: absolute; left: 29px; top: 82px; margin: 0;
    font-size: 15px; line-height: 22px;
  }
  .contact-list {
    position: absolute; left: 29px; top: 189px;
    list-style: none; margin: 0; padding: 0;
    font-size: 15px; line-height: 21.5px;
  }
  .contact-list li { display: flex; align-items: center; gap: 6px; }
  .contact-list svg { width: 13px; height: 13px; fill: var(--ink-light); flex: none; }
  .address {
    position: absolute; left: 29px; top: 291px; margin: 0;
    font-size: 15px; line-height: 21.5px; font-style: normal;
  }
  .crew-art {
    position: absolute; right: 0; top: 0;
    width: 300px; height: 363px;
    background: radial-gradient(circle at 60% 50%, var(--art-warm) 0%, var(--art-deep) 60%, var(--card-brown) 100%);
    clip-path: circle(200px at 210px 182px);
  }

  /* Brand side */
  .card-brand {
    left: 388px; top: 505px;
    width: 567px; height: 352px;
    background: var(--card-orange);
  }
  .brand {
    position: absolute; left: 0; right: 0; top: 124px;
    text-align: center; color: var(--ink-dark);
    font-family: "Oswald", sans-serif; font-weight: 600;
  }
  .brand-name {
    display: inline-flex; align-items: center; gap: 12px;
    font-size: 46px; line-height: 1; margin: 0;
  }
  .brand-dot {
    width: 30px; height: 30px; border-radius: 50%;
    background: var(--ink-dark);
  }
  .brand-sub { margin: 8px 0 0; font-size: 21px; line-height: 1; }
</style>
</head>
<body>
<main class="canvas">

  <section class="card card-contact">
    <h1 class="person-name">Sam Whitaker</h1>
    <p class="person-titles">Ridgeline certified Roof Inspector<br>Licensed Property Adjuster</p>
    <ul class="contact-list">
      <li><svg viewBox="0 0 16 16" aria-hidden="true"><path d="M2 6c0-2 2-4 6-4s6 2 6 4l-3 1-1-2H6L5 7 2 6zm2 2h8l1 6H3l1-6zm4 1.5a2 2 0 100 4 2 2 0 000-4z"/></svg>(555) 014-2200</li>
      <li><svg viewBox="0 0 16 16" aria-hidden="true"><path d="M4 1h8v14H4V1zm1.5 1.5v9h5v-9h-5zM8 12.5a.8.8 0 100 1.6.8.8 0 000-1.6z"/></svg>(555) 017-8391</li>
      <li><svg viewBox="0 0 16 16" aria-hidden="true"><path d="M1 3h14v10H1V3zm1.5 1.5v.4L8 9l5.5-4.1v-.4h-11zm0 2.3v4.7h11V6.8L8 10.8 2.5 6.8z"/></svg>sam@truenorthtx.com</li>
      <li><svg viewBox="0 0 16 16" aria-hidden="true"><path d="M8 1a7 7 0 110 14A7 7 0 018 1zm-2 3L4 6l1 2 2 1v2l2 2 1-3 2-1-1-3-2-1-1 1-2-2z"/></svg>www.TrueNorthGC.com</li>
    </ul>
    <address class="address">4810 Cedar Ridge Road Suite 110<br>Plano, TX 75093</address>
    <div class="crew-art" role="img" aria-label="Illustrated roofing crew with tools in front of a roof, set in a circular badge"></div>
  </section>

  <section class="card card-brand">
    <div class="brand">
      <p class="brand-name"><span>True</span><span class="brand-dot" aria-hidden="true"></span><span>North</span></p>
      <p class="brand-sub">General Contractors, Inc.</p>
    </div>
  </section>

</main>
</body>
</html>
```